Coastal Gin Label Design

We are needing a nautical/coastal themed label for our upcoming gin release.

We have saltbush, cucumber, juniper, and quandong being used in this gin.

Name of the Gin; Harbour Moons

The logo attached is the company logo, but doesn't have to be used on the front of the label, ie it can just be the name Fernwhistle somewhere on the front.
Bottle specs attached as well so you can accurately represent the bottle- this bottle is also clear.

Target Market(s)

Women 25- 45

Font styles to use
Serif
Decorative

Colors
d5edf4
86cae7
33a6d7
86cfc6
cfeae6
ffffff
f6faec
ecf7fb
fefeff

Requirements
Must have
• Ocean/Coastal vibe to the label
Nice to have
• Blues,Whites clean and crisp
Should not have
• No generic word art look to it.
A dark mood

```html
<!DOCTYPE html>
<html lang="en">
<head>
<meta charset="utf-8">
<title>Harbour Moons Gin — Label</title>
<link href="https://fonts.googleapis.com/css2?family=Mrs+Saint+Delafield&family=Playfair+Display:wght@600&family=IM+Fell+English&family=Barlow+Condensed:wght@400&display=swap" rel="stylesheet">
<style>
  :root {
    --backdrop: #e3ecf6;
    --paper: #f3f1ea;
    --paper-edge: #ece8de;
    --sand: #e6ddcf;
    --sand-light: #eee8dc;
    --navy: #2f4a78;
    --ink: #3a4a6e;
    --grey-ink: #6b6f78;
    --sea-pale: #d5edf4;
    --sea-mid: #86cae7;
    --sea-deep: #9ccbe6;
    --foam: #ffffff;
  }
  * { margin: 0; padding: 0; box-sizing: border-box; }
  html, body { width: 960px; height: 1200px; overflow: hidden; }
  body {
    background: radial-gradient(ellipse at 50% 45%, #f1f5fb 0%, var(--backdrop) 70%, #cfdcec 100%);
    display: flex; align-items: center; justify-content: center;
  }
  .label {
    position: relative;
    width: 720px; height: 866px;
    background: linear-gradient(180deg, var(--paper) 0%, var(--paper-edge) 100%);
    overflow: hidden;
  }
  .brand {
    position: absolute; top: 118px; left: 0; right: 0;
    text-align: center; color: var(--navy);
  }
  .brand-name {
    display: inline-flex; align-items: center; gap: 10px;
    font-family: "Playfair Display", serif; font-weight: 600;
    font-size: 28px; letter-spacing: 2px; text-transform: uppercase;
  }
  .brand-dot {
    width: 10px; height: 10px; border-radius: 50%; background: var(--navy);
  }
  .brand-place {
    margin-top: 4px;
    font-family: "IM Fell English", serif; font-size: 21px; color: var(--grey-ink);
  }
  .scenery { position: absolute; left: 0; top: 0; width: 720px; height: 866px; }
  .title {
    position: absolute; left: 40px; top: 268px;
    font-family: "Mrs Saint Delafield", cursive;
    color: var(--ink); line-height: 1;
  }
  .title-line1 { display: block; font-size: 150px; }
  .title-line2 { display: block; font-size: 150px; margin-left: 170px; margin-top: -20px; }
  .specs {
    position: absolute; left: 0; right: 0; top: 778px;
    text-align: center;
    font-family: "Barlow Condensed", sans-serif; font-size: 21px;
    color: var(--grey-ink); letter-spacing: 0.3px;
  }
  .specs .sep { display: inline-block; width: 2px; height: 15px; background: var(--grey-ink); margin: 0 8px; vertical-align: -1px; }
</style>
</head>
<body>
  <main class="label">
    <svg class="scenery" viewBox="0 0 720 866" xmlns="http://www.w3.org/2000/svg">
      <defs>
        <linearGradient id="sea" x1="0" y1="0" x2="0" y2="1">
          <stop offset="0" stop-color="var(--sea-pale)"/>
          <stop offset="0.45" stop-color="var(--sea-deep)"/>
          <stop offset="1" stop-color="var(--sea-pale)"/>
        </linearGradient>
      </defs>
      <g role="img" aria-label="Soft watercolour wash of sandy beach">
        <path d="M0 232 C80 214 160 226 250 218 C360 208 470 222 560 214 C620 210 690 220 720 216 L720 588 L0 588 Z" fill="var(--sand)"/>
        <path d="M0 262 C140 250 300 262 720 250 L720 300 C500 296 200 308 0 300 Z" fill="var(--sand-light)" opacity="0.6"/>
      </g>
      <g role="img" aria-label="Faint ship's wheel motif">
        <circle cx="605" cy="378" r="82" fill="none" stroke="var(--paper)" stroke-width="3" opacity="0.5"/>
      </g>
      <g role="img" aria-label="Watercolour ocean waves and white foam">
        <path d="M0 588 C120 570 260 584 400 574 C520 566 640 580 720 572 L720 660 L0 660 Z" fill="var(--foam)" opacity="0.9"/>
        <path d="M0 628 C150 618 330 632 500 622 C600 616 680 624 720 620 L720 802 C560 796 300 806 0 798 Z" fill="url(#sea)"/>
        <path d="M20 680 C200 670 420 684 700 676" stroke="var(--foam)" stroke-width="6" fill="none" opacity="0.5"/>
      </g>
    </svg>

    <header class="brand">
      <div class="brand-name"><span class="brand-dot"></span>Fernwhistle</div>
      <div class="brand-place">Distillery, WA</div>
    </header>

    <h1 class="title">
      <span class="title-line1">Harbour Moons</span>
      <span class="title-line2">Gin</span>
    </h1>

    <p class="specs">500ml<span class="sep"></span>40% ABV<span class="sep"></span>16 STD Drinks</p>
  </main>
</body>
</html>
```